New Innovative Counselling and psychotherapy Service needs Business Card design

Keep it simple and professional. On one side, just company name and logo (perhaps in all blue) and maybe a tag line.

On other side (all white) my name and Qualifications in centre

Industry/Entity Type

Health And Wellness

Contact Information for Business Card

Dara Whelby
Counsellor & Psychotherapist
BSc (Psychol.), BA, Dip. (Couns. & Psych.), PG.Cert (CBT), FGTrK, ONRE

I will also require Mobile no, Email and web site address of which I'll pass on to final designer.

Font styles to use
Sans Serif

Requirements
Must have
• My Logo Only and please use the colours in logo that is in it.
Should not have
• Any other images

```html
<!DOCTYPE html>
<html lang="en">
<head>
<meta charset="utf-8">
<title>BrightLane – Business Card</title>
<link rel="stylesheet" href="https://fonts.googleapis.com/css2?family=Work+Sans:wght@400;500;600&display=swap">
<style>
  :root {
    --stage: #2a2a2b;
    --card: #1d1d1e;
    --card-edge: #161617;
    --blue: #3aa8e4;
    --green: #7cc142;
    --white: #f2f2f2;
    --pattern-light: #5a5a5c;
    --pattern-dark: #232324;
  }
  * { box-sizing: border-box; margin: 0; padding: 0; }
  html, body { width: 1200px; height: 900px; overflow: hidden; }
  body {
    background: var(--stage);
    font-family: "Work Sans", Arial, sans-serif;
    color: var(--white);
    position: relative;
  }
  .card {
    position: absolute;
    left: 280px;
    width: 640px;
    height: 366px;
    background: var(--card);
    border: 1px solid var(--card-edge);
    overflow: hidden;
  }
  .card--brand { top: 60px; }
  .card--contact { top: 474px; }

  .brand-pattern {
    position: absolute;
    inset: 0;
    background: linear-gradient(100deg, var(--pattern-dark) 0%, var(--pattern-dark) 25%, var(--pattern-light) 100%);
    opacity: 0.55;
  }
  .brand-mark {
    position: absolute;
    display: flex;
    align-items: center;
    gap: 16px;
  }
  .brand-mark__dot {
    border-radius: 50%;
    background: var(--blue);
    flex: none;
  }
  .brand-mark__name {
    font-weight: 400;
    color: var(--white);
    letter-spacing: 0.5px;
  }
  .card--brand .brand-mark { left: 78px; top: 156px; }
  .card--brand .brand-mark__dot { width: 48px; height: 48px; }
  .card--brand .brand-mark__name { font-size: 26px; }

  .card--contact .brand-mark { left: 60px; top: 150px; }
  .card--contact .brand-mark__dot { width: 56px; height: 56px; }
  .card--contact .brand-mark__name { font-size: 30px; }

  .divider {
    position: absolute;
    left: 352px;
    top: 108px;
    width: 2px;
    height: 180px;
    background: var(--green);
  }
  .person {
    position: absolute;
    left: 374px;
    top: 104px;
    width: 250px;
  }
  .person__name {
    font-size: 31px;
    font-weight: 500;
    color: var(--blue);
    line-height: 1;
    margin-bottom: 6px;
  }
  .person__role,
  .person__quals {
    font-size: 15px;
    line-height: 1.3;
    letter-spacing: 0.3px;
  }
  .contact-list {
    list-style: none;
    margin-top: 12px;
  }
  .contact-list li {
    display: flex;
    align-items: center;
    gap: 8px;
    font-size: 16px;
    line-height: 1.6;
    letter-spacing: 0.3px;
  }
  .contact-list svg { width: 12px; height: 12px; flex: none; }
  .accent { color: var(--green); }
</style>
</head>
<body>
  <section class="card card--brand" aria-label="Card front">
    <div class="brand-pattern" role="img" aria-label="Repeating brand symbol pattern in dark grey tones"></div>
    <div class="brand-mark">
      <span class="brand-mark__dot"></span>
      <span class="brand-mark__name">BrightLane</span>
    </div>
  </section>

  <section class="card card--contact" aria-label="Card back">
    <div class="brand-mark">
      <span class="brand-mark__dot"></span>
      <span class="brand-mark__name">BrightLane</span>
    </div>
    <div class="divider"></div>
    <div class="person">
      <h1 class="person__name">DARA WHELBY</h1>
      <p class="person__role">Counsellor &amp; Psychotherapist</p>
      <p class="person__quals">BSc (Psychol.), BA, Dip. (Couns. &amp; Psych.), PG.Cert (CBT), FGTrK, ONRE</p>
      <ul class="contact-list">
        <li>
          <svg viewBox="0 0 12 12" aria-hidden="true"><path d="M2.5 1 L4.5 1 L5 3.5 L3.8 4.3 Q4.8 6.8 7.5 8 L8.3 6.8 L11 7.3 L11 9.5 Q10.5 11 9 11 Q2 10 1 3 Q1 1.3 2.5 1 Z" fill="var(--blue)"/></svg>
          555-014-2287
        </li>
        <li>
          <svg viewBox="0 0 12 12" aria-hidden="true"><rect x="1" y="2.5" width="10" height="7" fill="none" stroke="var(--blue)" stroke-width="1.2"/><path d="M1 2.5 L6 6.5 L11 2.5" fill="none" stroke="var(--blue)" stroke-width="1.2"/></svg>
          info@brightlane.com
        </li>
        <li>
          <svg viewBox="0 0 12 12" aria-hidden="true"><circle cx="6" cy="6" r="5" fill="none" stroke="var(--blue)" stroke-width="1"/><ellipse cx="6" cy="6" rx="2.2" ry="5" fill="none" stroke="var(--blue)" stroke-width="1"/><path d="M1 6 H11 M2 3.5 H10 M2 8.5 H10" stroke="var(--blue)" stroke-width="0.8"/></svg>
          <span>www.<span class="accent">brightlane</span>.com</span>
        </li>
      </ul>
    </div>
  </section>
</body>
</html>
```